Retail Sign for Houseplant Campaign

Sign will measure 3 to 4 foot tall by 22.2inches and place on rolling racks of houseplants for a retail promotion in The Birchwell Yard. The theme of the promotion will be "New Year, New You!" Selling points which should be on the sign are Houseplants give you a taste of nature, Houseplants boost air quality inside your home, Indoor plants reduce anxiety, Indoor plants make you more productive, Houseplants improve your concentration and memory.
Updates

Target Market(s)

People who love plants

Industry/Entity Type

Horticulture/ retail

Colors
00AB8E
00BBA5
67D7C9
C6EFE9
E9F9F6
59FF00
82FF00
B8FF75
E3FFCB
F4FFEA
FFF300
FFF600
FEFA6F
FFFEC7
FFFEE8

Requirements
Must have
• Must feel energetic and encourage people to buy plants. Should include 1-2 photos and the selling points listed

```html
<!DOCTYPE html>
<html lang="en">
<head>
<meta charset="utf-8">
<title>New Year, New You – Houseplant Sign</title>
<link rel="stylesheet" href="https://fonts.googleapis.com/css2?family=Encode+Sans+Condensed:wght@300;400&family=Lobster&display=swap">
<style>
  :root {
    --bar-1: #a3cf3c;
    --bar-2: #d8e325;
    --bar-3: #e3d21d;
    --bar-4: #f9e80c;
    --brand-green: #4a5d30;
    --panel-dark: #1a1a1a;
    --headline-green: #00a650;
    --headline-lime: #d9e21f;
    --pill-1: #0db592;
    --pill-2: #0fbca6;
    --pill-3: #78d0c5;
    --pill-4: #a9d4cb;
    --pill-5: #d0eeea;
    --pill-text: #121212;
  }
  * { margin: 0; padding: 0; box-sizing: border-box; }
  html, body { width: 1200px; height: 2560px; overflow: hidden; background: #fff; }
  .sign { position: relative; width: 1200px; height: 2560px; background: #fff; }

  .color-bar { position: absolute; top: 0; left: 0; width: 1200px; height: 52px; display: flex; }
  .color-bar span { flex: 1; }
  .color-bar span:nth-child(1) { background: var(--bar-1); }
  .color-bar span:nth-child(2) { background: var(--bar-2); }
  .color-bar span:nth-child(3) { background: var(--bar-3); }
  .color-bar span:nth-child(4) { background: var(--bar-4); }

  .brand { position: absolute; top: 170px; left: 0; width: 1200px; display: flex; justify-content: center; align-items: center; gap: 34px; }
  .brand-square { width: 120px; height: 120px; background: var(--brand-green); }
  .brand-name { font-family: "Encode Sans Condensed", sans-serif; font-weight: 400; font-size: 118px; letter-spacing: 2px; color: var(--brand-green); line-height: 1; }

  .hero-photo { position: absolute; top: 421px; left: 0; width: 1200px; height: 903px;
    background: linear-gradient(160deg, #eef0ec 0%, #dfe3dc 35%, #c9d3c0 55%, #e8d8d6 75%, #d8dce0 100%); }
  .photo-strip { position: absolute; top: 1324px; left: 0; width: 1200px; height: 302px; display: flex; }
  .photo-strip div { flex: 1; }
  .strip-family { background: linear-gradient(135deg, #e9ece8, #b8c6c8 60%, #6fb0b0); }
  .strip-potting { background: linear-gradient(135deg, #f2f2ef, #e4d3bf 55%, #c79b7a); }
  .strip-leaf { background: linear-gradient(135deg, #dedfe0, #c9c9c6 50%, #3e7a3a); }

  .message-panel { position: absolute; top: 1626px; left: 0; width: 1200px; height: 934px; background: var(--panel-dark); }
  .headline { position: absolute; left: 0; top: 0; width: 1200px; font-family: "Lobster", cursive; font-weight: 400; }
  .headline-line { position: absolute; white-space: nowrap; line-height: 1; font-size: 196px; }
  .headline-line.first { left: 152px; top: 88px; color: var(--headline-green); }
  .headline-line.second { left: 318px; top: 236px; color: var(--headline-lime); }

  .selling-points { position: absolute; top: 464px; left: 75px; width: 1055px; list-style: none; }
  .selling-points li { height: 66px; margin-bottom: 9px; border-radius: 33px; display: flex; align-items: center; justify-content: center;
    font-family: "Encode Sans Condensed", sans-serif; font-weight: 300; font-size: 47px; color: var(--pill-text); white-space: nowrap; }
  .selling-points li:nth-child(1) { background: var(--pill-1); }
  .selling-points li:nth-child(2) { background: var(--pill-2); }
  .selling-points li:nth-child(3) { background: var(--pill-3); }
  .selling-points li:nth-child(4) { background: var(--pill-4); }
  .selling-points li:nth-child(5) { background: var(--pill-5); }
</style>
</head>
<body>
<main class="sign">
  <div class="color-bar"><span></span><span></span><span></span><span></span></div>

  <header class="brand">
    <div class="brand-square"></div>
    <div class="brand-name">LEAFLINE GOODS</div>
  </header>

  <div class="hero-photo" role="img" aria-label="Young woman in a pink sweater relaxing on the floor of a bright living room, surrounded by monstera and potted houseplants, a laptop beside her"></div>

  <div class="photo-strip">
    <div class="strip-family" role="img" aria-label="Mother and daughter watering a snake plant with a teal watering can"></div>
    <div class="strip-potting" role="img" aria-label="Woman arranging a croton plant in a woven pot on a shelf"></div>
    <div class="strip-leaf" role="img" aria-label="Smiling woman wiping the leaves of a monstera plant"></div>
  </div>

  <section class="message-panel">
    <h1 class="headline">
      <span class="headline-line first">"New Year,</span>
      <span class="headline-line second">New You!"</span>
    </h1>
    <ul class="selling-points">
      <li>Houseplants give you a taste of nature</li>
      <li>Houseplants boost air quality inside your home</li>
      <li>Indoor plants reduce anxiety</li>
      <li>Indoor plants make you more productive</li>
      <li>Houseplants improve your concentration and memory</li>
    </ul>
  </section>
</main>
</body>
</html>
```